Recruitment of Trellan Staffing for the UK market

I want a website for the UK market to attract businesses and companies to come to us for Philipine labour. We want an information site that gives all information on what we do and how we can recruit Philippine labour.
This is a recruitment site for companies to contact us with their requirements for skilled workers coming from the Philipines over to the UK to work.

Target Market(s)

Uk Companies and businesses who want Philipine skilled workers

Industry/Entity Type

REcruitment

Coding

Number of Pages Required

5+ page

Font styles to use
Sans Serif

Colors
0054AA
0677BA
7BADD7
CADEEF
E8F1F8
0094D4
00A9DD
6FCCEA
C7EBF8
E9F6FB
EE7325
F08F49
F5BC92
FAE3D3
FDF4ED
EB3D1F
EC4F4E
F09395
F8D3D4
FCEDEE

Requirements
Must have
• Look professional and corperate with drop down menus for Home ,about, services,articles. training , contact us
Nice to have
• Look at Velmora recruitment- https://velmorarecruitment.example.co.uk/. This is my current site - https://www.trellanstaffing.example.com/
Should not have
• Cartoons or silly pictures , needs to be corperate looking

```html
<!DOCTYPE html>
<html lang="en">
<head>
<meta charset="utf-8">
<title>Trellan Staffing – Skilled Philippine Workers for UK Companies</title>
<link rel="stylesheet" href="https://fonts.googleapis.com/css2?family=Montserrat:wght@400;500;600;700&family=Oswald:wght@600;700&display=swap">
<style>
:root{
  --blue:#0054AA;
  --blue-mid:#0677BA;
  --sky:#0094D4;
  --sky-light:#C7EBF8;
  --orange:#EE7325;
  --peach:#FAE3D3;
  --peach-soft:#FDF4ED;
  --red:#EB3D1F;
  --ink:#1b1b1b;
  --text:#333333;
  --muted:#f6f7f8;
  --line:#e2e2e2;
  --white:#ffffff;
}
*{box-sizing:border-box;margin:0;padding:0}
html,body{width:1200px;height:3963px;overflow:hidden}
body{position:relative;background:var(--white);font-family:"Montserrat",sans-serif;color:var(--text)}
.abs{position:absolute}
.btn{position:absolute;display:flex;align-items:center;justify-content:center;background:var(--blue);color:var(--white);font-size:12.5px;font-weight:600;text-decoration:none}
.rule{position:absolute;height:3px;width:42px;background:var(--orange)}
.photo{position:absolute;border-radius:50%}
h2{position:absolute;font-weight:600;color:var(--ink);font-size:31px;letter-spacing:.2px}
.copy{position:absolute;font-size:12.5px;line-height:23px;color:var(--ink)}

/* header */
.brand{left:162px;top:22px;font-size:28px;font-weight:700;color:var(--red)}
.brand-mark{display:inline-block;width:16px;height:16px;background:var(--red);margin-right:10px;vertical-align:2px}
.nav{left:546px;top:36px;display:flex}
.nav a{font-size:13px;font-weight:600;color:var(--ink);text-decoration:none;margin-right:38px}
.nav a.active{color:var(--blue-mid)}

/* hero */
.hero-title{left:163px;top:190px;width:500px;z-index:2;white-space:nowrap;font-family:"Oswald",sans-serif;font-weight:700;font-size:38px;line-height:52px;letter-spacing:0;color:var(--blue);text-transform:uppercase}
.hero-title span{color:var(--orange)}

/* inquiry */
.inquiry{left:162px;top:543px;width:876px;height:188px;background:var(--peach)}
.inquiry h3{position:absolute;left:0;right:0;top:24px;text-align:center;font-size:23px;font-weight:600;color:var(--ink)}
.field{position:absolute;background:var(--white);font-size:12px;color:var(--ink);padding:0 20px;display:flex;align-items:center;height:36px}

.centered{text-align:center}

/* services */
.band{left:0;top:2764px;width:1200px;height:451px;background:var(--muted)}
.card{position:absolute;top:2889px;width:269px;height:237px;background:var(--white);border:1px solid var(--line);text-align:center}
.card .icon{position:absolute;left:109px;top:-27px;width:52px;height:52px;border-radius:50%;background:var(--white);border:1px solid var(--line)}
.card h4{position:absolute;left:0;right:0;top:52px;font-size:17px;font-weight:600;color:var(--ink)}
.card p{position:absolute;left:18px;right:18px;top:88px;font-size:12px;line-height:23px;color:var(--ink)}
.card .btn{left:78px;top:174px;width:112px;height:36px}

/* contact band */
.cta{left:0;top:3216px;width:1200px;height:450px;background:linear-gradient(90deg,#1c1d1f 0%,#2a2b2e 45%,#3b3f47 65%,#2c3a5c 100%)}
.cta h2{color:var(--white);left:163px;top:92px;font-size:34px}
.cta .copy{color:var(--white);left:163px;width:430px;font-size:12.5px}

/* footer */
.foot-h{position:absolute;top:3717px;font-size:15px;font-weight:600;color:var(--ink)}
.foot-link{position:absolute;font-size:12.5px;color:var(--ink)}
.foot-link::before{content:"›";margin-right:8px;font-weight:700}
.social{position:absolute;top:3768px;width:28px;height:28px;border-radius:50%;border:1px solid #c9c9c9}
.bottom{left:0;top:3914px;width:1200px;height:49px;background:var(--blue);color:var(--white);font-size:12.5px;display:flex;align-items:center;justify-content:center}
</style>
</head>
<body>

<!-- header -->
<div class="abs brand"><span class="brand-mark"></span>Trellan Staffing</div>
<nav class="abs nav">
  <a class="active" href="#">Home</a><a href="#">About</a><a href="#">Services</a><a href="#">Articles</a><a href="#">Training</a><a href="#">Contact Us</a>
</nav>

<!-- hero -->
<svg class="abs" style="left:660px;top:70px" width="540" height="460" viewBox="0 0 540 460">
  <ellipse cx="200" cy="230" rx="180" ry="210" fill="var(--peach)"/>
  <circle cx="63" cy="165" r="37" fill="#bfe4f7"/>
  <circle cx="476" cy="298" r="36" fill="var(--red)"/>
  <circle cx="285" cy="427" r="17" fill="var(--sky)"/>
</svg>
<div class="photo" role="img" aria-label="Nurse in blue scrubs holding a tablet" style="left:769px;top:80px;width:148px;height:148px;background:linear-gradient(160deg,#e6eef5,#6fa3d9)"></div>
<div class="photo" role="img" aria-label="Smiling engineer and office worker with hard hat and clipboard" style="left:932px;top:113px;width:212px;height:212px;background:linear-gradient(160deg,#f2efe9,#8aa5c4 60%,#e5b24a)"></div>
<div class="photo" role="img" aria-label="Group of healthcare workers in blue uniforms" style="left:679px;top:268px;width:253px;height:253px;background:linear-gradient(160deg,#e9e3de,#7aaee0 55%,#4d86c8)"></div>
<div class="photo" role="img" aria-label="Workers in a factory setting" style="left:963px;top:356px;width:118px;height:118px;background:linear-gradient(160deg,#d9d2cb,#8c6b58 60%,#b73b2d)"></div>

<h1 class="abs hero-title">Recruiting and placing<br>skilled <span>Philippine workers</span><br>into UK companies</h1>
<a class="btn" href="#" style="left:165px;top:361px;width:112px;height:36px">Contact Us</a>

<!-- quick inquiry -->
<form class="abs inquiry">
  <h3>Quick Inquiry</h3>
  <div class="field" style="left:63px;top:80px;width:243px">First name*</div>
  <div class="field" style="left:316px;top:80px;width:243px">Last name*</div>
  <div class="field" style="left:570px;top:80px;width:243px">Phone*</div>
  <div class="field" style="left:63px;top:126px;width:243px">Email*</div>
  <div class="field" style="left:316px;top:126px;width:374px">Message</div>
  <div class="btn" style="left:700px;top:126px;width:113px;height:36px">Submit Now</div>
</form>

<!-- about -->
<h2 class="centered" style="left:0;width:1200px;top:820px">What The Business is About</h2>
<div class="rule" style="left:579px;top:865px"></div>
<p class="copy centered" style="left:230px;width:740px;top:882px">We source skilled workers directly from the Philippines to work in the UK. With offices , training locations and specialist recruiters we can find the highest quality individuals to add value and resources to any UK buisness. We delivery quality based on vast experience over a number of years.</p>
<a class="btn" href="#" style="left:543px;top:969px;width:112px;height:36px">Contact Us</a>

<!-- working together -->
<h2 style="left:162px;top:1136px">Working Together</h2>
<div class="rule" style="left:162px;top:1185px"></div>
<p class="copy" style="left:162px;top:1200px;width:370px;font-size:17px;line-height:34px">We recruit the finest talent available with our dedicated 200 strong team.<br>Our centres are highlighted in <span style="color:var(--red);font-weight:700;text-decoration:underline">Red Dots</span> on the map.</p>
<a class="btn" href="#" style="left:162px;top:1349px;width:112px;height:37px">Contact Us</a>
<div class="abs" role="img" aria-label="Map of the Philippines marking centres in Baguio, Manila, Batangas, Bacolod and Davao" style="left:631px;top:1061px;width:392px;height:377px;background:radial-gradient(ellipse at 60% 50%,#eef4f9 0%,#f7f9fb 55%,#ffffff 80%)"></div>

<!-- what we do -->
<div class="photo" role="img" aria-label="Two businessmen reviewing work at a desk with UK and Philippine flags" style="left:162px;top:1526px;width:358px;height:358px;background:linear-gradient(160deg,#f1f1f1,#c9d3df 55%,#5f7da8)"></div>
<h2 style="left:600px;top:1600px">What We Do</h2>
<div class="rule" style="left:600px;top:1649px"></div>
<p class="copy" style="left:600px;top:1669px;width:440px">Our company has been estabilished in the Philippines for over 20 years. We have mainly been recruiting philippine workers for the off shore industry in asia but since brexit and the new rules on skilled workers entering the UK we have been working with UK companies who now have chance to recruit some of the finest hard working talent from the Philippines for their companies..</p>

<!-- how we help -->
<h2 style="left:162px;top:2008px">How We Help</h2>
<div class="rule" style="left:162px;top:2057px"></div>
<p class="copy" style="left:162px;top:2076px;width:430px">We work with companies to find skilled workers that meet the UK requirements for Visas and work permits. We guide you through the whole process and deliver highly trained people that add value to your business. We are here to help both the companies and the Philippino people to gain a better standard of living for their families.</p>
<div class="photo" role="img" aria-label="Engineer in hard hat and hi-vis jacket operating machinery" style="left:680px;top:1921px;width:358px;height:358px;background:linear-gradient(160deg,#8b9099,#4d5560 45%,#d7e63a 80%)"></div>

<!-- where to start -->
<div class="photo" role="img" aria-label="Two site engineers in hard hats reviewing a tablet" style="left:162px;top:2318px;width:358px;height:358px;background:linear-gradient(160deg,#7e7265,#c8b79d 45%,#f08f49 80%)"></div>
<h2 style="left:600px;top:2363px">Where To Start</h2>
<div class="rule" style="left:600px;top:2412px"></div>
<p class="copy" style="left:600px;top:2431px;width:440px">We need to know what your issues are and how we can understand the personnal you require , over what time frame and the number of employees you need. Once this is estabilished we start sourcing workers in the Philippines that meet your criteria while starting the process in the UK to be able to have all the documents in place to deliver your company hard working skilled individuals.</p>
<a class="btn" href="#" style="left:600px;top:2586px;width:112px;height:36px">Contact Us</a>

<!-- services -->
<div class="abs band"></div>
<div class="card" style="left:162px">
  <svg class="icon" viewBox="0 0 52 52"><rect x="17" y="14" width="18" height="24" rx="2" fill="none" stroke="var(--blue)" stroke-width="1.6"/><path d="M21 21h10M21 26h10M21 31h6" stroke="var(--blue)" stroke-width="1.6"/></svg>
  <h4>UK Skilled Workers List</h4>
  <p>The UK government since brexit have developed a new system based on points (similar to Australia)...</p>
  <a class="btn" href="#">Read More</a>
</div>
<div class="card" style="left:465px">
  <svg class="icon" viewBox="0 0 52 52"><rect x="18" y="13" width="16" height="26" rx="2" fill="none" stroke="var(--blue)" stroke-width="1.6"/><circle cx="26" cy="21" r="3" fill="none" stroke="var(--blue)" stroke-width="1.6"/><path d="M22 29h8M22 33h8" stroke="var(--blue)" stroke-width="1.6"/></svg>
  <h4>Sponsor Licence</h4>
  <p>If you have areas of your business that meet the entry requirements of skilled labour your next...</p>
  <a class="btn" href="#">Read More</a>
</div>
<div class="card" style="left:769px">
  <svg class="icon" viewBox="0 0 52 52"><circle cx="30" cy="29" r="8" fill="none" stroke="var(--blue)" stroke-width="1.6"/><path d="M30 25v4l3 2M16 38V22h8v16" fill="none" stroke="var(--blue)" stroke-width="1.6"/></svg>
  <h4>Recruitment Timeline</h4>
  <p>Brief us on the job profiles – this is passed on to our teams in the Philippines...</p>
  <a class="btn" href="#">Read More</a>
</div>

<!-- contact band -->
<section class="abs cta">
  <div class="abs" role="img" aria-label="Smiling engineers in hard hats holding a laptop and tablet" style="left:580px;top:0;width:620px;height:450px;background:linear-gradient(100deg,rgba(40,42,46,0) 0%,#2f4a86 55%,#233a6e 100%)"></div>
  <h2>Contact Us Today</h2>
  <p class="copy" style="top:160px">Please contact us today with your requirements, this can be care workers, chef, welders, pipe fitters, caravan cabinet makers, medical workers. The UK list of required skills is extensive &amp; the Philippines offersenglish speaking highly qualified hard working employees.</p>
  <p class="copy" style="top:258px;font-weight:600">Contact us today and make that first step to a highly motivated , quality skilled workforce.</p>
  <a class="btn" href="#" style="left:162px;top:317px;width:112px;height:36px;background:var(--white);color:var(--blue)">Contact Us</a>
</section>

<!-- footer -->
<div class="foot-h" style="left:162px">Quick Links</div>
<div class="rule" style="left:162px;top:3749px;height:2px;width:28px"></div>
<div class="foot-link" style="left:162px;top:3767px">Home</div>
<div class="foot-link" style="left:162px;top:3808px">About</div>
<div class="foot-link" style="left:162px;top:3850px">Services</div>
<div class="foot-link" style="left:266px;top:3767px">Articles</div>
<div class="foot-link" style="left:266px;top:3808px">Training</div>
<div class="foot-link" style="left:266px;top:3850px">Contact Us</div>

<div class="foot-h" style="left:440px">Contact Details</div>
<div class="rule" style="left:440px;top:3749px;height:2px;width:28px"></div>
<svg class="abs" style="left:440px;top:3768px" width="14" height="18" viewBox="0 0 14 18"><path d="M7 1a6 6 0 0 1 6 6c0 4-6 10-6 10S1 11 1 7a6 6 0 0 1 6-6z" fill="var(--blue)"/><circle cx="7" cy="7" r="2.2" fill="#fff"/></svg>
<p class="copy" style="left:468px;top:3764px;font-size:12.5px;line-height:20px;width:260px">14 Larkfield Row, Brindlemoor<br>BM4 7QT United Kingdom</p>
<svg class="abs" style="left:440px;top:3818px" width="16" height="16" viewBox="0 0 16 16"><path d="M3 1l3 3-2 2c1 2 3 4 5 5l2-2 3 3-2 3C7 15 1 9 1 3z" fill="var(--blue)"/></svg>
<p class="copy" style="left:468px;top:3815px">07700 900418</p>
<svg class="abs" style="left:440px;top:3850px" width="18" height="13" viewBox="0 0 18 13"><rect x="0.5" y="0.5" width="17" height="12" fill="var(--blue)"/><path d="M1 1l8 6 8-6" fill="none" stroke="#fff" stroke-width="1.3"/></svg>
<p class="copy" style="left:468px;top:3845px">sales@trellanstaffing.example.com</p>

<div class="foot-h" style="left:798px">Follow Us On</div>
<div class="rule" style="left:798px;top:3749px;height:2px;width:28px"></div>
<div class="social" role="img" aria-label="Social profile link" style="left:801px"></div>
<div class="social" role="img" aria-label="Social profile link" style="left:835px"></div>
<div class="social" role="img" aria-label="Social profile link" style="left:869px"></div>
<div class="social" role="img" aria-label="Social profile link" style="left:904px"></div>
<div class="abs brand" style="left:800px;top:3822px;font-size:24px"><span class="brand-mark" style="width:14px;height:14px"></span>Trellan Staffing</div>

<div class="abs bottom">© 2023 Trellan Staffing Ltd. All Rights Reserved</div>

</body>
</html>
```